Dietitian needs awesome business card

I need a contemporary design that's eye catching but professional.
My card is to given to doctors, specialists and patients alike.
I manage patients with chronic diseases
I have uploaded my logo and current business card, I would also like the other Certified Clinical Nutritionist logo incorporated into the design

Target Market(s)

Doctors, specialists and patients

Industry/Entity Type

Healthcare

Contact Information for Business Card

www.brightfieldnutrition.com.au
Ph: 0427 561 903
Fax: 6457 2183
email: marcus.k.diet@fernmail.com
Space on the back of the card with: Appointment date, Appointment time and appointment location

Font styles to use
Serif

Colors
fbee3e
876aae
ffc214

Requirements
Must have
• My Logo
• Certified Clinical Nutritionist Logo
• My 4 locations - Pinebrook Medical Centre, North Corrin Health, Hollis Medical, Ashcombe Doctors Surgery
Nice to have
• I like the colours in my current business card

```html
<!DOCTYPE html>
<html lang="en">
<head>
<meta charset="utf-8">
<title>Brightfield Nutrition &amp; Dietetics – Business Card</title>
<link href="https://fonts.googleapis.com/css2?family=Marcellus&family=Lora:ital,wght@0,400;0,500;1,400&display=swap" rel="stylesheet">
<style>
  :root {
    --page-bg: #e9e6e1;
    --card-white: #ffffff;
    --card-shade: #eef0f0;
    --brand-blue: #1479c4;
    --brand-green: #8cc63f;
    --brand-green-light: #c5e35a;
    --text-grey: #7a7d80;
    --badge-orange: #f0a030;
    --dots: #8a8d90;
  }
  * { box-sizing: border-box; margin: 0; padding: 0; }
  html, body {
    width: 1200px; height: 1023px; overflow: hidden;
    background: var(--page-bg);
  }
  .canvas {
    width: 1200px; height: 1023px;
    display: flex; flex-direction: column; align-items: center; justify-content: center;
    gap: 40px;
  }
  .card {
    position: relative;
    width: 760px; height: 450px;
    background: linear-gradient(160deg, var(--card-white) 40%, var(--card-shade));
    box-shadow: 0 6px 18px rgba(0,0,0,.18);
    overflow: hidden;
  }
  .band {
    position: absolute; left: 0; right: 0;
    height: 58px;
    background: linear-gradient(90deg, var(--brand-green-light), var(--brand-green));
    border-bottom: 12px solid var(--card-white);
    display: flex; align-items: center;
  }
  .band::after {
    content: ""; position: absolute; left: 0; right: 0; bottom: -9px;
    height: 3px; background: var(--brand-blue);
  }
  .band-title {
    font-family: "Marcellus", serif;
    color: var(--brand-blue);
    font-size: 34px; letter-spacing: 1px;
    text-transform: uppercase;
  }

  /* Front */
  .front .brand {
    position: absolute; left: 150px; top: 90px;
    display: flex; align-items: center; gap: 18px;
  }
  .brand-dot {
    width: 62px; height: 62px; border-radius: 50%;
    background: var(--brand-green);
  }
  .brand-name {
    font-family: "Marcellus", serif;
    color: var(--brand-blue);
    font-size: 36px; line-height: 1.1;
  }
  .front .band { top: 215px; padding-left: 150px; }
  .contact-grid {
    position: absolute; left: 150px; top: 318px;
    display: grid; grid-template-columns: auto 1px auto;
    column-gap: 22px; row-gap: 12px; align-items: center;
  }
  .contact-divider { grid-row: 1 / span 2; grid-column: 2; background: var(--text-grey); height: 70px; opacity: .6; }
  .contact-item {
    display: flex; align-items: center; gap: 10px;
    font-family: "Lora", serif;
  }
  .contact-item.phone { color: var(--brand-blue); font-size: 26px; font-weight: 500; }
  .contact-item.line { color: var(--text-grey); font-size: 17px; }
  .icon { width: 20px; height: 20px; flex: none; }

  /* Back */
  .back .band { top: 40px; justify-content: flex-end; padding-right: 60px; }
  .location {
    position: absolute; left: 60px; top: 150px;
    font-family: "Lora", serif;
  }
  .location-title {
    font-family: "Marcellus", serif;
    color: var(--brand-green); font-size: 24px; letter-spacing: 1px;
    margin-bottom: 10px;
  }
  .location-list { list-style: none; color: var(--brand-blue); font-style: italic; font-size: 18px; line-height: 1.55; }
  .appointment-fields {
    position: absolute; right: 60px; top: 160px; width: 340px;
    font-family: "Lora", serif; color: var(--text-grey); font-size: 20px;
  }
  .field { display: flex; align-items: baseline; gap: 8px; margin-bottom: 38px; }
  .field-line { flex: 1; border-bottom: 2px dotted var(--dots); transform: translateY(-4px); }
  .credential-badge {
    position: absolute; left: 60px; bottom: 40px;
    width: 130px; height: 74px; border-radius: 6px;
    background: var(--badge-orange);
  }
</style>
</head>
<body>
<main class="canvas">

  <section class="card front" aria-label="Card front">
    <div class="brand">
      <span class="brand-dot"></span>
      <span class="brand-name">Brightfield Nutrition &amp; Dietetics</span>
    </div>
    <div class="band"><h1 class="band-title">Marcus Keller</h1></div>
    <div class="contact-grid">
      <div class="contact-item phone">
        <svg class="icon" viewBox="0 0 20 20" aria-hidden="true"><rect x="2" y="8" width="16" height="10" rx="2" fill="var(--brand-green)"/><rect x="5" y="2" width="10" height="7" fill="none" stroke="var(--brand-green)" stroke-width="2"/></svg>
        6457 2183
      </div>
      <span class="contact-divider"></span>
      <div class="contact-item phone">
        <svg class="icon" viewBox="0 0 20 20" aria-hidden="true"><rect x="5" y="1" width="10" height="18" rx="2" fill="var(--brand-green)"/><rect x="7" y="4" width="6" height="10" fill="#fff"/></svg>
        0427 561 903
      </div>
      <div class="contact-item line">
        <svg class="icon" viewBox="0 0 20 20" aria-hidden="true"><rect x="2" y="4" width="16" height="12" rx="2" fill="var(--brand-green)"/><path d="M2 5l8 6 8-6" fill="none" stroke="#fff" stroke-width="1.6"/></svg>
        marcus.k.diet@fernmail.com
      </div>
      <div class="contact-item line">
        <svg class="icon" viewBox="0 0 20 20" aria-hidden="true"><circle cx="10" cy="10" r="8" fill="var(--brand-green)"/><path d="M2 10h16M10 2c-4 4-4 12 0 16M10 2c4 4 4 12 0 16" fill="none" stroke="#fff" stroke-width="1.3"/></svg>
        www.brightfieldnutrition.com.au
      </div>
    </div>
  </section>

  <section class="card back" aria-label="Card back">
    <div class="band"><h2 class="band-title">Appointment</h2></div>
    <div class="location">
      <h3 class="location-title">LOCATION</h3>
      <ul class="location-list">
        <li>Pinebrook Medical Centre</li>
        <li>North Corrin Health</li>
        <li>Hollis Medical</li>
        <li>Ashcombe Doctors Surgery</li>
      </ul>
    </div>
    <div class="appointment-fields">
      <div class="field">Date:<span class="field-line"></span></div>
      <div class="field">Time:<span class="field-line"></span></div>
    </div>
    <div class="credential-badge" role="img" aria-label="Certified Clinical Nutritionist credential badge"></div>
  </section>

</main>
</body>
</html>
```